SnackOrbit!!! A Vending Machine Business Looking for an attractive website.

We are a vending machine business in Northern Michigan. We have changed our name and have rebranded our company. We would like an attractive website that shares who we are, what services we provide, the products we offer in our machines, along with a form businesses can fill out to see if they are a good fit for our company. I would like to have a Home Page, About SnackOrbit, Why Choose SnackOrbit?, Products & Services, Contact Us (With a Login Option), and a page with a questionnaire for thos interested in getting a FREE Vending Machine.

Target Market(s)

Businesses, Campgrounds, Schools, and many more in Northern Michigan

Industry/Entity Type

Vending Machines

Coding

Coded - Design and coding required

Number of Pages Required

5+ page

Requirements
Must have
• An inviting and enticing Home Page. I want to get my potential clients engaged in our website.
Nice to have
• Possibly background photos from Northern Michigan
Should not have
• A corporate feel. I do not want a boring website.

```html
<!DOCTYPE html>
<html lang="en">
<head>
<meta charset="utf-8">
<title>SnackOrbit – Vending Machines in Northern Michigan</title>
<link href="https://fonts.googleapis.com/css2?family=Outfit:wght@400;500;600;700&display=swap" rel="stylesheet">
<style>
:root{
  --green:#2a5a1e;
  --green-dark:#1f4716;
  --purple:#22144b;
  --purple-deep:#1c1140;
  --ink:#23124b;
  --text:#555;
  --field:#f1f1f1;
  --white:#fff;
}
*{box-sizing:border-box;margin:0;padding:0}
html,body{width:1200px;height:4392px;overflow:hidden}
body{font-family:'Outfit',sans-serif;color:var(--text);background:var(--white);position:relative}
.abs{position:absolute}
.rule{display:block;width:78px;height:3px;background:var(--green)}
.rule.center{margin:0 auto}
.btn{display:inline-block;background:var(--green);color:var(--white);font-weight:600;font-size:13px;letter-spacing:.3px;text-transform:uppercase;text-align:center;line-height:36px;padding:0 17px}
.section-title{font-weight:700;color:var(--ink);font-size:40px;text-align:center;margin-top:14px}

/* header */
.site-header{position:absolute;top:0;left:0;width:1200px;height:75px;background:var(--white)}
.brand{position:absolute;left:145px;top:18px;display:flex;align-items:center;gap:8px;font-weight:700;font-size:30px;color:var(--purple)}
.brand-mark{width:14px;height:14px;background:var(--green)}
.main-nav{position:absolute;left:392px;top:0;height:75px;display:flex;align-items:center;gap:22px;font-size:13px;font-weight:500;color:#333}
.main-nav .active{color:var(--green);position:relative}
.main-nav .active::after{content:"";position:absolute;left:0;right:0;bottom:-8px;height:2px;background:var(--green)}
.nav-divider{width:1px;height:40px;background:#ddd}
.login{color:var(--green);display:flex;align-items:center;gap:6px}

/* hero */
.hero{position:absolute;top:75px;left:0;width:1200px;height:600px;background:linear-gradient(100deg,#9ab6b0 0%,#5f7c7e 20%,#c9b39a 40%,#5a4a40 60%,#2a2530 80%,#3d3140 100%)}
.hero-copy{position:absolute;left:733px;top:214px;color:var(--white)}
.hero-copy .eyebrow{font-size:13px;font-weight:600}
.hero-copy h1{font-size:60px;font-weight:700;line-height:1;margin:10px 0 10px}
.hero-copy p{font-size:13px}
.hero-copy .btn-light{display:inline-block;margin-top:16px;background:var(--white);color:var(--green);font-weight:700;font-size:13px;line-height:36px;padding:0 16px}
.hero-arrows{position:absolute;top:484px;left:556px;display:flex;gap:8px}
.circle-arrow{width:40px;height:40px;border-radius:50%;background:var(--white);display:flex;align-items:center;justify-content:center}

/* who */
.who-copy{position:absolute;left:143px;top:815px;width:430px}
.who-copy h2{font-size:40px;font-weight:700;color:var(--ink);margin:14px 0 14px}
.who-copy p{font-size:12px;line-height:20px;text-align:justify}
.who-copy .btn{margin-top:14px}
.who-visual{position:absolute;left:583px;top:752px;width:498px;height:375px}
.who-photo{position:absolute;left:17px;top:17px;width:456px;height:332px;background:linear-gradient(90deg,#2b3a55,#c0453a 30%,#2f5b9a 55%,#d8c46a 75%,#4a5c70)}

/* services */
.services{position:absolute;top:1216px;left:0;width:1200px}
.tile{position:absolute;width:380px;height:241px}
.tile-label{position:absolute;right:0;bottom:0;width:210px;height:40px;background:var(--green-dark);color:var(--white);font-size:15px;display:flex;align-items:center;justify-content:space-between;padding:0 10px 0 16px}
.tile-label .dot{width:22px;height:22px;border-radius:50%;background:var(--white);display:flex;align-items:center;justify-content:center}

/* machines */
.machines{position:absolute;top:1903px;left:0;width:1200px}
.card{position:absolute;top:88px;width:287px;height:395px;border:2px solid #ddd;background:var(--white);padding:0 26px}
.card .machine{margin:26px auto 0;width:100px;height:172px;background:linear-gradient(180deg,#2d2d2d,#4a4a4a 60%,#2d2d2d);border:3px solid #1e1e1e}
.card h3{font-size:20px;font-weight:600;color:var(--ink);margin-top:24px}
.card p{font-size:12px;line-height:20px;margin:8px 0 14px}
.side-arrow{position:absolute;top:285px;width:34px;height:34px;border-radius:50%;background:#eee;display:flex;align-items:center;justify-content:center}

/* why */
.why{position:absolute;top:2494px;left:0;width:1200px;height:636px;background:var(--purple)}
.why .rule{background:var(--white);margin-top:96px}
.why .section-title{color:var(--white)}
.feature{position:absolute;top:182px;width:205px;color:var(--white)}
.feature .icon{width:114px;height:114px;background:var(--green);display:flex;align-items:center;justify-content:center}
.feature h3{font-size:17px;font-weight:600;line-height:19px;margin:24px 0 14px}
.feature p{font-size:12px;line-height:20px;text-align:justify}

/* contact */
.contact{position:absolute;top:3130px;left:0;width:1200px;height:615px}
.contact .rule{margin-top:74px}
.field{position:absolute;background:var(--field);font-size:12px;color:#444;padding:0 22px;line-height:55px}
.submit{position:absolute;left:542px;top:460px;width:116px;line-height:36px;padding:0}

/* cta */
.cta{position:absolute;top:3745px;left:0;width:1200px;height:279px;background:var(--green)}
.cta .rule{position:absolute;left:143px;top:82px;background:var(--white)}
.cta h2{position:absolute;left:143px;top:100px;color:var(--white);font-size:38px;font-weight:700;line-height:48px}
.cta p{position:absolute;left:662px;top:110px;width:400px;color:var(--white);font-size:12px;line-height:24px}

/* footer */
.footer{position:absolute;top:4024px;left:0;width:1200px;height:290px;background:var(--purple)}
.footer-brand{position:absolute;left:180px;top:76px;font-size:32px;font-weight:700;color:var(--white)}
.footer-about{position:absolute;left:185px;top:148px;width:228px;font-size:13px;line-height:20px;color:var(--white);text-align:justify}
.footer h4{position:absolute;top:78px;color:var(--white);font-size:20px;font-weight:600}
.footer ul{position:absolute;top:120px;list-style:none;color:var(--white);font-size:13px;line-height:24px}
.footer .links li::before{content:"»";margin-right:14px}
.footer .contact-list li{display:flex;gap:14px}
.footer .contact-list svg{margin-top:6px;flex:none}
.socials{position:absolute;left:917px;top:122px;display:flex;gap:6px}
.socials span{width:30px;height:30px;border-radius:50%;background:var(--green);display:block}
.bottom-bar{position:absolute;top:4314px;left:0;width:1200px;height:78px;background:var(--purple-deep);color:var(--white);font-size:13px;text-align:center;line-height:78px}
</style>
</head>
<body>

<header class="site-header">
  <div class="brand"><span class="brand-mark"></span>SnackOrbit</div>
  <nav class="main-nav">
    <span class="active">Home</span>
    <span>About SnackOrbit</span>
    <span>Why Choose SnackOrbit?</span>
    <span>Products &amp; Services</span>
    <span>Contact Us</span>
    <span class="nav-divider"></span>
    <span class="login"><svg width="11" height="12" viewBox="0 0 11 12"><circle cx="5.5" cy="3" r="3" fill="#2a5a1e"/><path d="M0 12c0-4 2.5-5.5 5.5-5.5S11 8 11 12z" fill="#2a5a1e"/></svg>Login</span>
  </nav>
</header>

<section class="hero" role="img" aria-label="Woman choosing a snack on a lit vending machine at night">
  <div class="hero-copy">
    <div class="eyebrow">Welcome To</div>
    <h1>SnackOrbit</h1>
    <p>At SnackOrbit, we don't just vend snacks—we curate cravings.</p>
    <span class="btn-light">GET STARTED</span>
  </div>
  <div class="hero-arrows">
    <span class="circle-arrow"><svg width="10" height="14"><path d="M8 1 2 7l6 6" stroke="#333" stroke-width="1.6" fill="none"/></svg></span>
    <span class="circle-arrow"><svg width="10" height="14"><path d="M2 1l6 6-6 6" stroke="#333" stroke-width="1.6" fill="none"/></svg></span>
  </div>
</section>

<section class="who">
  <div class="who-copy">
    <span class="rule"></span>
    <h2>Who We Are</h2>
    <p>Welcome to SnackOrbit, where snacking meets delight! We're not just about vending machines; we're your culinary companions, your flavor curators, and your secret stash of happiness. Dana and Miles, the dynamic duo behind SnackOrbit, have a passion for all things tasty. With backgrounds in sales and a penchant for personal connections, they've transformed the vending experience into an art form.</p>
    <span class="btn">Learn More</span>
  </div>
  <div class="who-visual">
    <svg class="abs" width="498" height="375" viewBox="0 0 498 375">
      <polygon points="0,0 115,0 0,115" fill="#2a5a1e"/>
      <polygon points="498,213 498,375 333,375" fill="#2a5a1e"/>
    </svg>
    <div class="who-photo" role="img" aria-label="Rows of colourful snack packs inside vending machines"></div>
  </div>
</section>

<section class="services">
  <span class="rule center"></span>
  <h2 class="section-title">What Services We Provide</h2>
  <div class="tile" style="left:15px;top:91px;background:linear-gradient(135deg,#2a1e18,#7a5a3e 50%,#2b2220)" role="img" aria-label="Office break room with a snack vending machine">
    <div class="tile-label">Lorem ipsum dolor<span class="dot"><svg width="8" height="10"><path d="M2 1l4 4-4 4" stroke="#222" stroke-width="1.6" fill="none"/></svg></span></div></div>
  <div class="tile" style="left:411px;top:91px;background:linear-gradient(90deg,#1f4fa0,#5c86c8 45%,#c9352b 75%,#e6e6e6)" role="img" aria-label="Row of drink and snack vending machines">
    <div class="tile-label">Lorem ipsum dolor<span class="dot"><svg width="8" height="10"><path d="M2 1l4 4-4 4" stroke="#222" stroke-width="1.6" fill="none"/></svg></span></div></div>
  <div class="tile" style="left:805px;top:91px;background:linear-gradient(90deg,#7a3a30,#c45a40 35%,#3a5c78 70%,#2a3448)" role="img" aria-label="Young woman browsing a vending machine">
    <div class="tile-label">Lorem ipsum dolor<span class="dot"><svg width="8" height="10"><path d="M2 1l4 4-4 4" stroke="#222" stroke-width="1.6" fill="none"/></svg></span></div></div>
  <div class="tile" style="left:15px;top:356px;background:linear-gradient(90deg,#1b2438,#4d5f80 45%,#2e4fb0 70%,#9aa3b0)" role="img" aria-label="Technician servicing a vending machine">
    <div class="tile-label">Lorem ipsum dolor<span class="dot"><svg width="8" height="10"><path d="M2 1l4 4-4 4" stroke="#222" stroke-width="1.6" fill="none"/></svg></span></div></div>
  <div class="tile" style="left:411px;top:356px;background:linear-gradient(90deg,#d6d6d2,#8a8a86 45%,#2b2b2b 60%,#6a5a48)" role="img" aria-label="Snack vending machine in a bright lobby">
    <div class="tile-label">Lorem ipsum dolor<span class="dot"><svg width="8" height="10"><path d="M2 1l4 4-4 4" stroke="#222" stroke-width="1.6" fill="none"/></svg></span></div></div>
  <div class="tile" style="left:805px;top:356px;background:linear-gradient(90deg,#2c3a3a,#5a6a66 40%,#c04a3e 65%,#3e7ac0 85%,#d8b040)" role="img" aria-label="Close view of snack packs on vending shelves">
    <div class="tile-label">Lorem ipsum dolor<span class="dot"><svg width="8" height="10"><path d="M2 1l4 4-4 4" stroke="#222" stroke-width="1.6" fill="none"/></svg></span></div></div>
</section>

<section class="machines">
  <span class="rule center"></span>
  <h2 class="section-title">We Offer in Our Machines</h2>
  <span class="side-arrow" style="left:55px"><svg width="8" height="12"><path d="M6 1 1 6l5 5" stroke="#333" stroke-width="1.5" fill="none"/></svg></span>
  <div class="card" style="left:141px">
    <div class="machine" role="img" aria-label="Snack vending machine"></div>
    <h3>Lorem ipsum dolor</h3>
    <p>Lorem ipsum dolor sit amet, consec tetur adipiscing elit, sed do eiusmod tempor incididunt</p>
    <span class="btn">Learn More</span>
  </div>
  <div class="card" style="left:457px">
    <div class="machine" role="img" aria-label="Snack vending machine"></div>
    <h3>Lorem ipsum dolor</h3>
    <p>Lorem ipsum dolor sit amet, consec tetur adipiscing elit, sed do eiusmod tempor incididunt</p>
    <span class="btn">Learn More</span>
  </div>
  <div class="card" style="left:770px">
    <div class="machine" role="img" aria-label="Snack vending machine"></div>
    <h3>Lorem ipsum dolor</h3>
    <p>Lorem ipsum dolor sit amet, consec tetur adipiscing elit, sed do eiusmod tempor incididunt</p>
    <span class="btn">Learn More</span>
  </div>
  <span class="side-arrow" style="left:1111px"><svg width="8" height="12"><path d="M2 1l5 5-5 5" stroke="#333" stroke-width="1.5" fill="none"/></svg></span>
</section>

<section class="why">
  <span class="rule center"></span>
  <h2 class="section-title">Why Choose SnackOrbit?</h2>
  <div class="feature" style="left:143px">
    <div class="icon"><svg width="60" height="60" viewBox="0 0 60 60" fill="none" stroke="#fff" stroke-width="2"><path d="M30 22c-3-6-13-5-13 2 0 6 13 13 13 13s13-7 13-13c0-7-10-8-13-2z"/><path d="M6 34l8 12h12M54 34l-8 12H34"/></svg></div>
    <h3>Local Love</h3>
    <p>We celebrate the heart of Michigan by partnering with local legends. Say hello to Pine Ridge Jerky and North Shore Potato Chips—our hometown heroes. Their flavors dance on your taste buds, and we're thrilled to bring them straight to your workplace.</p>
  </div>
  <div class="feature" style="left:382px">
    <div class="icon"><svg width="60" height="60" viewBox="0 0 60 60" fill="none" stroke="#fff" stroke-width="2"><circle cx="30" cy="30" r="20"/><rect x="22" y="24" width="16" height="14" rx="2"/><path d="M22 30h16"/></svg></div>
    <h3>Unleash Your Cravings</h3>
    <p>SnackOrbit isn't bound by corporate ties. We're the rebels of the vending world. Craving a bag of crispy, kettle-cooked chips? Done. Hankering for jerky that packs a punch? We've got you covered. Our machines are like treasure chests, waiting for you to unlock flavor magic.</p>
  </div>
  <div class="feature" style="left:620px">
    <div class="icon"><svg width="60" height="60" viewBox="0 0 60 60" fill="none" stroke="#fff" stroke-width="2"><path d="M14 46V24l6-10 4 2-2 10h8v20z"/><circle cx="40" cy="38" r="9"/><path d="M36 38l3 3 5-6"/></svg></div>
    <h3>Quality Meets Convenience</h3>
    <p>Imagine this: You're mid-meeting, and your stomach growls. Fear not! SnackOrbit's machines offer top-notch snacks and beverages. It's like having a mini food festival at your fingertips.</p>
  </div>
  <div class="feature" style="left:859px">
    <div class="icon"><svg width="60" height="60" viewBox="0 0 60 60" fill="none" stroke="#fff" stroke-width="2"><path d="M18 48V36c-6-6-4-22 10-24 12-1 18 8 16 16l4 6h-4v6h-8v8"/><path d="M30 30l8 8M34 38l8-8"/></svg></div>
    <h3>Pandemic-Proof &amp; Recession-Ready</h3>
    <p>Life throws curveballs, but SnackOrbit stands strong. Our vending machines are the unsung heroes of resilience. Rain or shine, they're there, serving up joy.</p>
  </div>
</section>

<section class="contact">
  <span class="rule center"></span>
  <h2 class="section-title">Get In Touch</h2>
  <div class="field" style="left:203px;top:173px;width:250px">Name</div>
  <div class="field" style="left:474px;top:173px;width:250px">Email</div>
  <div class="field" style="left:747px;top:173px;width:250px">Phone</div>
  <div class="field" style="left:203px;top:247px;width:385px">Company</div>
  <div class="field" style="left:610px;top:247px;width:387px">Subject</div>
  <div class="field" style="left:203px;top:318px;width:794px;height:127px">Message</div>
  <span class="btn submit">Submit</span>
</section>

<section class="cta">
  <span class="rule"></span>
  <h2>Ready to experience<br>the SnackOrbit difference?</h2>
  <p>Sign up now and let's connect. Taste the future of snacking firsthand! Contact us today and explore how our vending magic can elevate your space.</p>
</section>

<footer class="footer">
  <div class="footer-brand">SnackOrbit</div>
  <p class="footer-about">Our customized vending solutions bring flavor, convenience, and community to Northern Michigan.</p>
  <h4 style="left:476px">Information</h4>
  <ul class="links" style="left:476px">
    <li>Home</li><li>About SnackOrbit</li><li>Why Choose</li><li>SnackOrbit?</li><li>Products &amp; Services</li><li>Contact Us</li>
  </ul>
  <h4 style="left:673px">Contact</h4>
  <ul class="contact-list" style="left:673px">
    <li><svg width="12" height="12" viewBox="0 0 12 12"><path d="M2 1l2 0 1 3-1.5 1a7 7 0 0 0 3.5 3.5L8 7l3 1v2c0 1-1 1-1 1C5 11 1 7 1 2c0 0 0-1 1-1z" fill="#fff"/></svg><span>Phone :<br>+1 888 888 8888</span></li>
    <li><svg width="12" height="10" viewBox="0 0 12 10"><rect width="12" height="10" fill="#fff"/><path d="M0 0l6 5 6-5" stroke="#22144b" fill="none"/></svg><span>Email :<br>info@snackorbit-mail.com</span></li>
    <li><svg width="12" height="14" viewBox="0 0 12 14"><path d="M6 14S1 8 1 5a5 5 0 0 1 10 0c0 3-5 9-5 9z" fill="#fff"/><circle cx="6" cy="5" r="2" fill="#22144b"/></svg><span>Address<br>45 Birchwood Lane</span></li>
  </ul>
  <h4 style="left:917px">Follow us</h4>
  <div class="socials"><span></span><span></span><span></span></div>
</footer>
<div class="bottom-bar">© Copyrights 2024 Company name | All Rights Reserved</div>

</body>
</html>
```